Schriftdesign für Shop-Header Bild (Schmuckhandel) / Online-Marketing Material
Wir verkaufen Schmuck im Onlineshop mit Herz
Wir benötigen den vorgegebenen Text in schöner Form, Farbe und Größe harmonisch eingefügt, in unserem Bild.
Folgender Text soll sich schick ins Bild einfügen oder in 3-D vielleicht in Schriftfarbe gold hervorheben:
Mit ganzem Herzen für Sie da!
Ihr Online -Juwelier mit Herz
Siehe auch unser altes Bild mit Text, im Shop, wie es nicht aussehen sollte: www.sonnenflocke.de

```html
<!DOCTYPE html>
<html lang="de">
<head>
<meta charset="utf-8">
<title>Sonnenflocke – Online-Juwelier</title>
<link href="https://fonts.googleapis.com/css2?family=Lato:wght@400;700&family=Anton&family=Yanone+Kaffeesatz:wght@500&family=Raleway:wght@500&display=swap" rel="stylesheet">
<style>
  :root{
    --white:#ffffff;
    --red:#d0141c;
    --red-soft:#e8727a;
    --nav:#6b6769;
    --field:#efefef;
    --ink:#222222;
    --muted:#6a6a6a;
    --gold:#e3c27e;
    --gold-deep:#3a2410;
    --dots:#cfcfcf;
  }
  *{margin:0;padding:0;box-sizing:border-box}
  html,body{width:1200px;height:1200px;overflow:hidden;background:var(--white)}
  body{position:relative;font-family:'Lato',sans-serif;color:var(--ink)}

  .brand{position:absolute;left:255px;top:268px;display:flex;align-items:center;gap:8px}
  .brand-dot{width:14px;height:14px;border-radius:50%;background:var(--red)}
  .brand-name{font-family:'Lato',sans-serif;font-weight:700;font-size:19px;color:var(--red)}

  .meta-links{position:absolute;top:238px;right:238px;display:flex;gap:14px;font-size:8.6px}
  .meta-links a{color:var(--ink);text-decoration:none}
  .meta-links a.is-active{color:var(--red)}

  .search-label{position:absolute;left:440px;top:256px;font-size:12.4px;color:var(--ink)}
  .search-label .caret{display:inline-block;width:0;height:0;border-left:4px solid transparent;border-right:4px solid transparent;border-top:5px solid var(--red);margin-left:6px;vertical-align:middle}
  .search-field{position:absolute;left:440px;top:276px;width:303px;height:29px;background:var(--field);display:flex;align-items:center;justify-content:space-between;padding:0 10px 0 17px;font-size:9.6px;color:var(--muted)}
  .cart-field{position:absolute;left:784px;top:277px;width:178px;height:29px;background:var(--field);display:flex;align-items:center;justify-content:space-between;padding:0 16px 0 18px;font-size:9.6px;color:var(--red-soft)}

  .main-nav{position:absolute;left:0;top:331px;width:1200px;height:31px;background:var(--nav)}
  .main-nav .notch{position:absolute;left:276px;top:31px;width:0;height:0;border-left:30px solid transparent;border-right:30px solid transparent;border-top:20px solid var(--nav)}
  .main-nav ul{list-style:none;position:absolute;left:347px;top:0;height:31px;display:flex;align-items:center;gap:28px;font-family:'Raleway',sans-serif;font-weight:500;font-size:12.4px;color:var(--white);text-transform:uppercase}
  .nav-notch-cut{position:absolute;left:276px;top:331px;width:0;height:0;border-left:30px solid transparent;border-right:30px solid transparent;border-top:20px solid var(--white)}

  .hero{position:absolute;left:0;top:362px;width:1200px;height:308px;background:linear-gradient(100deg,#d8d6d2 0%,#eeebe6 30%,#e9e2d6 55%,#d7c7ad 80%,#c8ae86 100%);overflow:hidden}
  .hero-jewel{position:absolute;left:462px;top:90px;width:210px;height:200px;border-radius:50%;background:radial-gradient(circle at 40% 40%,#f3e2b4,#c8a458 70%,rgba(200,164,88,0) 72%)}
  .hero-title{position:absolute;left:232px;top:30px;font-family:'Anton',sans-serif;font-size:58px;letter-spacing:0.5px;color:var(--gold);text-transform:uppercase;line-height:1;
    text-shadow:1px 1px 0 var(--gold-deep),2px 2px 0 var(--gold-deep),3px 3px 0 var(--gold-deep),4px 4px 0 var(--gold-deep),5px 5px 0 var(--gold-deep),6px 7px 6px rgba(0,0,0,.35)}
  .hero-sub{position:absolute;left:682px;top:122px;font-family:'Yanone Kaffeesatz',sans-serif;font-weight:500;font-size:33px;color:var(--red);transform:skewX(-8deg);letter-spacing:0.5px;text-transform:uppercase}

  .trust-badge{position:absolute;left:737px;top:690px;width:104px;height:62px}
  .benefits{position:absolute;left:727px;top:761px;width:230px;border-top:3px dotted var(--dots);border-bottom:3px dotted var(--dots);height:143px;padding-top:22px}
  .benefits ul{list-style:none}
  .benefits li{display:flex;align-items:center;gap:6px;color:var(--red);font-size:12px;height:28.5px}

  .store-note{position:absolute;left:255px;top:760px;font-size:13.5px;color:var(--muted)}
  .store-note a{font-size:11px;color:var(--muted);text-decoration:none}
  .store-banner{position:absolute;left:255px;top:793px;width:442px;height:117px;background:linear-gradient(90deg,#1c1c1c 0%,#2a2a2a 45%,#b0762c 62%,#6a6a6a 80%,#8a8a8a 100%);border:1px solid #ddd}
</style>
</head>
<body>

  <div class="brand">
    <span class="brand-dot"></span>
    <span class="brand-name">sonnenflocke.de</span>
  </div>

  <nav class="meta-links">
    <a class="is-active" href="#">Startseite</a>
    <a href="#">Anmelden</a>
    <a href="#">Mein Konto</a>
    <a href="#">Newsletter abonnieren</a>
    <a href="#">Kontakt</a>
  </nav>

  <div class="search-label">Nach welchem Artikel suchen Sie?<span class="caret"></span></div>
  <div class="search-field">
    <span>Suchen nach</span>
    <svg width="22" height="20" viewBox="0 0 22 20" aria-hidden="true">
      <path d="M11 19 C2 12 0 9 0 5.5 A5.5 5.5 0 0 1 11 4 A5.5 5.5 0 0 1 22 5.5 C22 9 20 12 11 19Z" fill="var(--red)"/>
      <circle cx="10" cy="7.5" r="2.6" fill="none" stroke="#fff" stroke-width="1.4"/>
      <line x1="12" y1="9.5" x2="14" y2="11.5" stroke="#fff" stroke-width="1.6"/>
    </svg>
  </div>
  <div class="cart-field">
    <span>Ihr Warenkorb ist leer.</span>
    <svg width="16" height="18" viewBox="0 0 16 18" aria-hidden="true">
      <path d="M5 5 V3.5 A3 3 0 0 1 11 3.5 V5" fill="none" stroke="var(--red)" stroke-width="1.5"/>
      <rect x="0" y="5" width="16" height="13" rx="1.5" fill="var(--red)"/>
      <path d="M8 14.5 C5 12.5 4.5 11.5 4.5 10.3 A1.7 1.7 0 0 1 8 9.8 A1.7 1.7 0 0 1 11.5 10.3 C11.5 11.5 11 12.5 8 14.5Z" fill="#fff"/>
    </svg>
  </div>

  <nav class="main-nav">
    <ul>
      <li>Kreuz-Anhänger</li>
      <li>Anhänger/Versch.</li>
      <li>Foto-Medaillons</li>
      <li>Ohrschmuck</li>
      <li>Accessoires</li>
    </ul>
  </nav>
  <div class="nav-notch-cut"></div>

  <section class="hero">
    <div role="img" aria-label="Goldener Herzanhänger an feiner Kette auf cremefarbenem Seidenstoff" style="position:absolute;inset:0">
      <div class="hero-jewel"></div>
    </div>
    <h1 class="hero-title">Mit ganzem Herzen für Sie da!</h1>
    <p class="hero-sub">Ihr Online-Juwelier mit Herz</p>
  </section>

  <svg class="trust-badge" viewBox="0 0 104 62" role="img" aria-label="Siegel für sicheres Einkaufen">
    <rect x="40" y="19" width="62" height="24" rx="3" fill="#d8b868"/>
    <circle cx="31" cy="31" r="31" fill="#243a7a"/>
    <circle cx="31" cy="31" r="18" fill="#d8b868"/>
  </svg>

  <div class="benefits">
    <ul>
      <li><svg width="24" height="20" viewBox="0 0 24 20" aria-hidden="true"><path d="M12 19 C3 12 1 9 1 5.8 A5.5 5.5 0 0 1 12 4 A5.5 5.5 0 0 1 23 5.8 C23 9 21 12 12 19Z" fill="none" stroke="var(--red-soft)" stroke-width="1.6"/></svg>Versand innerhalb von 24 Stunden</li>
      <li><svg width="24" height="20" viewBox="0 0 24 20" aria-hidden="true"><path d="M12 19 C3 12 1 9 1 5.8 A5.5 5.5 0 0 1 12 4 A5.5 5.5 0 0 1 23 5.8 C23 9 21 12 12 19Z" fill="none" stroke="var(--red-soft)" stroke-width="1.6"/></svg>schneller, persönlicher Service</li>
      <li><svg width="24" height="20" viewBox="0 0 24 20" aria-hidden="true"><path d="M12 19 C3 12 1 9 1 5.8 A5.5 5.5 0 0 1 12 4 A5.5 5.5 0 0 1 23 5.8 C23 9 21 12 12 19Z" fill="none" stroke="var(--red-soft)" stroke-width="1.6"/></svg>Kundenzufriedenheit an erster Stelle</li>
      <li><svg width="24" height="20" viewBox="0 0 24 20" aria-hidden="true"><path d="M12 19 C3 12 1 9 1 5.8 A5.5 5.5 0 0 1 12 4 A5.5 5.5 0 0 1 23 5.8 C23 9 21 12 12 19Z" fill="none" stroke="var(--red-soft)" stroke-width="1.6"/></svg>sichere Zahlungsmethoden</li>
    </ul>
  </div>

  <p class="store-note">Besuchen Sie auch unseren AUREVIA-Schmuck Store: <a href="#">hier</a></p>
  <div class="store-banner" role="img" aria-label="Werbebanner des Aurevia-Schmuck-Stores: Goldschmelze mit Flamme in einer Werkstatt"></div>

</body>
</html>
```